BrivoTerna. Lantern of the Steady Harvest. Business card

Professional business card for BrivoTerna (Lantern of the Steady Harvest)
My rationale: Strategy-> Execution-> Results-> Value that lead to the BrivoTerna name: We put the Lantern of the Steady Harvest.
We deliver value to our customers helping them at defining a good strategy (cyan arrow). 90% of well formulated strategies fail due to poor execution so we also consider strategical execution very important (green arrow). Due to the execution we obtain the results (blue arrow). Finally, the results provide feedback to redefine strategy, and the new strategy has to be executed and new results obtained providing new feedback and on and on. It's like a wheel that finally, must create corporate value: value for shareholders, staholders, employees, providers...-

Target Market(s)

CEOs and steering comitees , invewrnent funds

Industry/Entity Type

Business Consultant

Contact Information for Business Card

Teodoro Vinsquel
CEO & Founder
teodoro.vinsquel@brivoterna-example.com
Mobile: +34 655.803.912
www.brivoterna-example.com

Colors

Designer to choose colors to be used in the design.

Requirements
Nice to have
• Nice to hace the words: Strategy, execution, results
• Nice to vave the claim: Lantern of the Steady Harvest
• The three colors should be shown:
• cyan for STRATEGY
• green for EXECUTION
• blue for RESULTS
Should not have
• Complete black background

```html
<!DOCTYPE html>
<html lang="en">
<head>
<meta charset="utf-8">
<title>BrivoTerna — Business Card</title>
<link rel="stylesheet" href="https://fonts.googleapis.com/css2?family=Arimo:wght@400;700&display=swap">
<style>
  :root{
    --cyan:#1f9cd3;
    --green:#8cbd3a;
    --navy:#1f3587;
    --ink:#2a2f3a;
    --paper:#f7f8f8;
    --stage:#e6e4df;
    --pattern-light:#5fb5e0;
  }
  *{box-sizing:border-box;margin:0;padding:0}
  html,body{width:1200px;height:1200px;overflow:hidden}
  body{
    background:var(--stage);
    font-family:"Arimo",Arial,sans-serif;
    display:flex;flex-direction:column;align-items:center;justify-content:center;gap:40px;
  }
  .card{
    position:relative;width:900px;height:514px;overflow:hidden;
    box-shadow:0 6px 18px rgba(0,0,0,.12);
  }
  /* Front */
  .card-front{background:var(--paper);color:var(--ink)}
  .wordmark{
    position:absolute;left:64px;top:200px;
    font-weight:700;font-size:64px;letter-spacing:-1px;color:var(--navy);
  }
  .divider{
    position:absolute;left:440px;top:110px;width:2px;height:270px;background:var(--navy);
  }
  .details{position:absolute;left:470px;top:112px;right:20px}
  .person-name{font-weight:700;font-size:38px;color:var(--navy);line-height:1.1}
  .person-title{font-size:24px;color:#444;margin-top:4px}
  .contact-list{list-style:none;margin-top:24px}
  .contact-item{display:flex;align-items:center;gap:12px;font-size:20px;color:#333;margin-bottom:14px;white-space:nowrap}
  .contact-icon{width:22px;height:22px;flex:none}
  .pillar-band{position:absolute;left:0;right:0;top:400px;height:58px;display:flex}
  .pillar{
    flex:1;display:flex;align-items:center;justify-content:center;
    color:#fff;font-size:30px;
  }
  .pillar-strategy{background:var(--cyan)}
  .pillar-execution{background:var(--green)}
  .pillar-results{background:var(--navy)}
  /* Back */
  .card-back{background:var(--cyan)}
  .back-pattern{
    position:absolute;inset:0;
    background:linear-gradient(135deg,var(--cyan) 0%,var(--pattern-light) 50%,var(--cyan) 100%);
    opacity:.55;
  }
  .wordmark-back{
    position:absolute;right:70px;bottom:60px;
    font-weight:700;font-size:60px;letter-spacing:-1px;color:#fff;
  }
</style>
</head>
<body>

<section class="card card-front" aria-label="Business card front">
  <div class="wordmark">BrivoTerna</div>
  <div class="divider"></div>
  <div class="details">
    <div class="person-name">Teodoro Vinsquel</div>
    <div class="person-title">CEO &amp; Founder</div>
    <ul class="contact-list">
      <li class="contact-item">
        <svg class="contact-icon" viewBox="0 0 24 24" aria-hidden="true"><path fill="none" stroke="#1f3587" stroke-width="2.4" stroke-linecap="round" d="M5 20c2-6 6-12 12-14M15 4l4 3"/></svg>
        +34 655.803.912
      </li>
      <li class="contact-item">
        <svg class="contact-icon" viewBox="0 0 24 24" aria-hidden="true"><rect x="2" y="5" width="20" height="14" fill="none" stroke="#1f3587" stroke-width="2.4"/><path d="M2 5l10 8 10-8" fill="none" stroke="#1f3587" stroke-width="2.4"/></svg>
        teodoro.vinsquel@brivoterna-example.com
      </li>
      <li class="contact-item">
        <svg class="contact-icon" viewBox="0 0 24 24" aria-hidden="true"><circle cx="12" cy="12" r="9" fill="#1f3587"/><path d="M3 12h18M12 3c-4 5-4 13 0 18M12 3c4 5 4 13 0 18" fill="none" stroke="#fff" stroke-width="1"/></svg>
        www.brivoterna-example.com
      </li>
    </ul>
  </div>
  <div class="pillar-band">
    <div class="pillar pillar-strategy">Strategy</div>
    <div class="pillar pillar-execution">Execution</div>
    <div class="pillar pillar-results">Results</div>
  </div>
</section>

<section class="card card-back" aria-label="Business card back">
  <div class="back-pattern" role="img" aria-label="Faint repeating brand pattern in light cyan"></div>
  <div class="wordmark-back">BrivoTerna</div>
</section>

</body>
</html>
```